Seeking a new website design for electrical contracting company

Brisket & Vane electrical contracting needs a new website for brisket-vane.example

We are looking for modern and something real cool with motion for a landing page. we have some cool images from our photo shoot. maybe even 3d motion our existing logo. we would like something we can edit with news and events and update a past project page. Also allow to take payment
stock images at
https://lorapellwinphotos.picvault-demo.example/Brisket-and-Vane

Target Market(s)

construction , home owners , business owners,

Industry/Entity Type

construction , electrical

Coding

Number of Pages Required

5+ page

Font styles to use
Serif
Sans Serif

Colors
0054AA
0677BA
7BADD7
CADEEF
E8F1F8
0094D4
00A9DD
6FCCEA
C7EBF8
E9F6FB
FFF300
FFF600
FEFA6F
FFFEC7
FFFEE8

Requirements
Must have
• excitement, motion, selling professionalism,

```html
<!DOCTYPE html>
<html lang="en">
<head>
<meta charset="utf-8">
<title>Brisket &amp; Vane Electrical Contractors</title>
<link href="https://fonts.googleapis.com/css2?family=Montserrat:wght@600;700;800&family=Mulish:wght@400;600;700&display=swap" rel="stylesheet">
<style>
:root{
  --blue:#0054AA;
  --blue-mid:#0677BA;
  --blue-soft:#7BADD7;
  --blue-pale:#CADEEF;
  --blue-mist:#E8F1F8;
  --cyan:#0094D4;
  --cyan-bright:#00A9DD;
  --cyan-soft:#6FCCEA;
  --cyan-pale:#C7EBF8;
  --cyan-mist:#E9F6FB;
  --yellow:#FFF300;
  --yellow-warm:#FFF600;
  --yellow-soft:#FEFA6F;
  --yellow-pale:#FFFEC7;
  --ink:#14203a;
  --muted:#44506a;
  --white:#ffffff;
}
*{box-sizing:border-box;margin:0;padding:0}
html,body{width:1200px;height:5146px;overflow:hidden}
body{position:relative;background:var(--white);font-family:"Mulish",sans-serif;color:var(--ink)}
.abs{position:absolute}
.display{font-family:"Montserrat",sans-serif;font-weight:800;text-transform:uppercase}
.accent{color:var(--cyan)}

/* buttons */
.btn{position:absolute;display:flex;align-items:center;justify-content:center;height:44px;padding:0 22px 0 14px;font-family:"Montserrat",sans-serif;font-weight:700;font-size:13px;text-transform:uppercase;text-decoration:none;white-space:nowrap}
.btn::after{content:"";position:absolute;right:-16px;top:0;width:22px;height:100%;transform:skewX(-20deg);z-index:-1}
.btn-blue{background:var(--blue);color:var(--white)}
.btn-blue::after{background:var(--yellow)}
.btn-yellow{background:var(--yellow);color:var(--blue)}
.btn-yellow::after{background:var(--cyan-bright)}

/* header */
.site-header{top:0;left:0;width:1200px;height:88px}
.brand{left:110px;top:18px;display:flex;align-items:center;gap:10px}
.brand-dot{width:46px;height:46px;border-radius:50%;background:var(--blue)}
.brand-name{font-family:"Montserrat",sans-serif;font-weight:800;font-size:22px;color:var(--blue);text-transform:uppercase;line-height:1;white-space:nowrap}
.main-nav{left:468px;top:34px;display:flex;gap:34px;font-family:"Montserrat",sans-serif;font-weight:600;font-size:14px;text-transform:uppercase}
.main-nav a{color:var(--ink);text-decoration:none}
.main-nav a.active{color:var(--blue);font-weight:700}

/* hero */
.hero{left:28px;top:88px;width:1146px;height:600px;border-radius:20px;overflow:hidden;
  background:
  radial-gradient(ellipse 30% 60% at 86% 20%,rgba(111,204,234,.55),transparent 70%),
  radial-gradient(ellipse 45% 25% at 70% 62%,rgba(255,243,0,.18),transparent 70%),
  radial-gradient(ellipse 70% 35% at 72% 80%,rgba(0,169,221,.75),transparent 70%),
  radial-gradient(ellipse 55% 30% at 60% 95%,rgba(0,84,170,.9),transparent 70%),
  linear-gradient(100deg,#02040c 0%,#040a1c 42%,#06204a 72%,#0677BA 100%)}
.hero-copy{left:82px;top:118px;color:var(--white);width:520px}
.hero-eyebrow{font-size:24px;color:var(--yellow)}
.hero-title{font-size:52px;margin-top:8px;line-height:1.05;white-space:nowrap}
.hero-sub{font-family:"Montserrat",sans-serif;font-weight:600;font-size:25px;margin-top:12px;text-transform:uppercase}
.hero-text{font-size:14px;line-height:26px;margin-top:10px;width:470px}

/* about */
.about-title{left:110px;top:800px;font-size:40px;color:var(--blue);white-space:nowrap}
.about-sub{left:110px;top:856px;font-family:"Montserrat",sans-serif;font-weight:700;font-size:21px;color:var(--cyan);text-transform:uppercase}
.about-text{left:552px;top:784px;width:540px;font-size:13px;line-height:27px;color:var(--ink)}
.about-text p+p{margin-top:14px}

.feature-card{top:1046px;width:494px;height:246px;padding:36px 18px;overflow:hidden}
.feature-card h3{font-family:"Montserrat",sans-serif;font-weight:800;font-size:20px;text-transform:uppercase}
.feature-card p{font-size:13px;line-height:26px;width:200px;margin-top:18px}
.feature-card .link{display:inline-block;margin-top:16px;font-size:12px;font-weight:700;text-transform:uppercase;text-decoration:underline;color:inherit}
.card-team{left:92px;background:var(--blue-mist);color:var(--blue)}
.card-team p{color:var(--muted)}
.card-services{left:612px;background:var(--yellow-warm);color:var(--blue)}
.card-services p{color:var(--blue)}
.team-ring{position:absolute;left:262px;top:24px;width:222px;height:222px;border-radius:50%;border:1px solid var(--blue-soft)}
.team-photo{position:absolute;border-radius:50%}
.globe{position:absolute;right:-14px;top:14px;width:214px;height:240px;border-radius:50%;
  background:radial-gradient(circle at 38% 36%,var(--yellow-pale),var(--yellow-soft) 55%,#f2e640 100%);
  box-shadow:inset 0 0 0 1px rgba(0,84,170,.15)}

/* video */
.video{left:110px;top:1400px;width:980px;height:506px;border-radius:30px;
  background:
  radial-gradient(ellipse 22% 18% at 50% 40%,rgba(123,173,215,.55),transparent 70%),
  radial-gradient(ellipse 10% 8% at 14% 12%,rgba(230,170,70,.55),transparent 70%),
  radial-gradient(ellipse 12% 9% at 78% 14%,rgba(230,170,70,.55),transparent 70%),
  radial-gradient(ellipse 14% 10% at 82% 82%,rgba(230,170,70,.5),transparent 70%),
  radial-gradient(ellipse 12% 10% at 14% 78%,rgba(230,170,70,.5),transparent 70%),
  linear-gradient(135deg,#0e3561 0%,#1d5a8c 45%,#0c2a52 100%)}
.play{left:569px;top:1623px}

/* section heads */
.sec-mark{width:30px;height:30px;border-radius:50%;background:var(--blue);left:585px}
.sec-title{width:1200px;left:0;text-align:center;font-family:"Montserrat",sans-serif;font-weight:700;font-size:34px;color:var(--blue);text-transform:uppercase}

.news-intro{left:160px;top:2094px;width:880px;text-align:center;font-size:14px;line-height:26px;color:var(--ink)}
.hex-photo{left:155px;top:2170px}
.date-badge{background:var(--yellow);color:var(--blue);font-family:"Montserrat",sans-serif;font-weight:700;font-size:13px;display:flex;align-items:center;justify-content:center;white-space:nowrap}
.lead-caption{left:110px;top:2624px;width:440px;font-family:"Montserrat",sans-serif;font-weight:600;font-size:14px;line-height:28px}
.event{left:600px;width:490px;height:144px;background:var(--blue-mist);display:flex;align-items:center;gap:18px;padding:0 14px}
.event-img{width:132px;height:118px;flex:none}
.event-date{font-size:12px;font-weight:700;color:var(--blue)}
.event p{font-size:13px;line-height:26px;color:var(--ink)}
.event a{font-size:13px;font-weight:700;color:var(--blue)}

/* projects */
.projects{left:0;top:2772px;width:1200px;height:868px;background:var(--cyan-mist)}
.project-img{position:absolute}

/* latest news */
.news-card{top:3855px;width:306px;height:445px;background:var(--white);box-shadow:0 4px 14px rgba(0,84,170,.1);border-radius:8px;overflow:hidden}
.news-card .photo{height:208px}
.news-card .date-badge{position:absolute;left:14px;top:194px;width:96px;height:26px;font-size:11px}
.news-card h4{margin:42px 14px 0;font-family:"Montserrat",sans-serif;font-weight:700;font-size:13px;text-transform:uppercase;color:var(--ink)}
.news-card p{margin:10px 14px 0;font-size:13px;line-height:26px;color:var(--muted)}
.news-card .btn{left:14px;bottom:32px}

/* cta */
.cta{left:0;top:4368px;width:1200px;height:270px;background:linear-gradient(90deg,var(--blue) 0%,#004690 100%);color:var(--white)}
.cta-title{left:110px;top:102px;font-family:"Montserrat",sans-serif;font-weight:700;font-size:30px;line-height:46px;text-transform:uppercase}
.contact-item{top:86px;width:240px;text-align:center;font-size:15px;line-height:26px}
.contact-item .ico{width:38px;height:38px;border-radius:50%;background:var(--yellow);margin:0 auto 12px;display:flex;align-items:center;justify-content:center}
.contact-item strong{display:block;font-family:"Montserrat",sans-serif;font-weight:700}

/* footer */
.footer-brand{left:0;top:4740px;width:1200px;display:flex;flex-direction:column;align-items:center;gap:16px}
.footer-brand .brand-dot{width:90px;height:90px}
.footer-brand .brand-name{font-size:34px}
.footer-nav{left:0;top:4940px;width:1200px;display:flex;justify-content:center;gap:46px;font-family:"Montserrat",sans-serif;font-weight:600;font-size:14px;text-transform:uppercase}
.footer-nav a{color:var(--ink);text-decoration:none}
.copyright{left:0;top:4994px;width:1200px;text-align:center;font-family:"Montserrat",sans-serif;font-weight:600;font-size:13px;text-transform:uppercase}
.social{left:524px;top:5040px;display:flex;gap:10px}
.social span{width:28px;height:28px;border-radius:50%;border:2px solid var(--blue)}
.social span:first-child{background:var(--yellow);border-color:var(--yellow)}
</style>
</head>
<body>

<header class="site-header abs">
  <div class="brand abs"><span class="brand-dot"></span><span class="brand-name">Brisket &amp; Vane</span></div>
  <nav class="main-nav abs">
    <a class="active" href="#">Home</a><a href="#">About Us</a><a href="#">Services</a><a href="#">Projects</a><a href="#">News</a>
  </nav>
  <a class="btn btn-blue" href="#" style="left:942px;top:22px;height:42px">Contact Us</a>
</header>

<section class="hero abs" role="img" aria-label="Neon streaks of blue light rushing into the distance">
  <div class="hero-copy abs">
    <div class="hero-eyebrow display">Welcome to</div>
    <h1 class="hero-title display">Brisket &amp; Vane</h1>
    <div class="hero-sub">Electrical Contractors</div>
    <p class="hero-text">Excepteur sint occaecat cupidatat non proident, sunt in culpa qui officia deserunt mollit anim id est laborum.</p>
  </div>
  <a class="btn btn-yellow" href="#" style="left:82px;top:337px">Get Started</a>
</section>

<section class="about">
  <h2 class="about-title abs display">Brisket &amp; Vane</h2>
  <div class="about-sub abs">Electrical Contractors</div>
  <a class="btn btn-blue" href="#" style="left:110px;top:906px">Learn More</a>
  <div class="about-text abs">
    <p>Lorem ipsum dolor sit amet, consectetur adipiscing elit, sed do eiusmod tempor incididunt ut labore et dolore magna aliqua. Ut enim ad minim veniam, quis nostrud exercitation ullamco laboris nisi ut aliquip ex ea commodo consequat.</p>
    <p>Duis aute irure dolor in reprehenderit in voluptate velit esse cillum dolore eu fugiat nulla pariatur. Excepteur sint occaecat cupidatat non proident, sunt in culpa qui officia deserunt mollit anim id est laborum.</p>
  </div>

  <div class="feature-card card-team abs">
    <h3>Our Team</h3>
    <p>Duis aute irure dolor in esse cillum dolore eu fugiat nulla pariatur.</p>
    <a class="link" href="#">View Our Teams</a>
    <div class="team-ring"></div>
    <div class="team-photo" style="left:250px;top:0;width:130px;height:130px;background:radial-gradient(circle at 50% 45%,var(--cyan-soft),var(--cyan))" role="img" aria-label="Team member portrait"></div>
    <div class="team-photo" style="left:380px;top:64px;width:116px;height:116px;background:radial-gradient(circle at 50% 45%,var(--blue-mid),var(--blue))" role="img" aria-label="Team member portrait"></div>
    <div class="team-photo" style="left:244px;top:140px;width:132px;height:132px;background:radial-gradient(circle at 50% 45%,var(--blue-pale),var(--blue-soft))" role="img" aria-label="Team member portrait"></div>
  </div>
  <div class="feature-card card-services abs">
    <h3>Our Services</h3>
    <p>Duis aute irure dolor in esse cillum dolore eu fugiat nulla pariatur.</p>
    <a class="link" href="#">View Our Teams</a>
    <div class="globe" role="img" aria-label="Wireframe globe of connected lines"></div>
  </div>
</section>

<section class="video abs" role="img" aria-label="Isometric scene of a laptop on a circuit board with shipping containers and trucks"></section>
<svg class="play abs" width="62" height="62" viewBox="0 0 62 62" aria-label="Play video"><circle cx="31" cy="31" r="28" fill="none" stroke="#fff" stroke-width="3"/><path d="M25 19 L43 31 L25 43 Z" fill="#fff"/></svg>

<section class="news-events">
  <span class="sec-mark abs" style="top:1998px"></span>
  <h2 class="sec-title abs" style="top:2040px">News and <span class="accent">Events</span></h2>
  <p class="news-intro abs">Duis aute irure dolor in reprehenderit in voluptate velit esse cillum dolore eu fugiat nulla pariatur. Excepteur sint occaecat cupidatat non proident, sunt in culpa qui officia deserunt mollit anim id est laborum.</p>
  <svg class="hex-photo abs" width="375" height="432" viewBox="0 0 375 432" role="img" aria-label="Electricians working on a pylon at sunset">
    <defs>
      <linearGradient id="sunset" x1="0" y1="0" x2="0" y2="1"><stop offset="0" stop-color="#b7c4d2"/><stop offset=".45" stop-color="#e4b06a"/><stop offset=".7" stop-color="#c5783e"/><stop offset="1" stop-color="#3d3140"/></linearGradient>
    </defs>
    <polygon points="187,0 375,108 375,324 187,432 0,324 0,108" fill="#0054AA"/>
    <polygon points="187,40 330,122 330,300 187,382 44,300 44,122" fill="url(#sunset)"/>
  </svg>
  <div class="date-badge abs" style="left:110px;top:2570px;width:130px;height:40px">APRIL 18,2025</div>
  <p class="lead-caption abs">Lorem ipsum dolor sit amet, consectetur adipiscing elit, sed do eiusmod tempor incididunt</p>

  <article class="event abs" style="top:2181px">
    <div class="event-img" style="background:radial-gradient(ellipse 70% 30% at 55% 55%,#c35ae0,transparent 70%),linear-gradient(135deg,#12061f,#3d1266,#12061f)" role="img" aria-label="Purple light waves"></div>
    <div><div class="event-date">APRIL 18,2025</div><p>Duis aute irure dolor in reprehenderit in voluptate velit esse cillum nulla pariatur.</p><a href="#">Learn More</a></div>
  </article>
  <article class="event abs" style="top:2348px">
    <div class="event-img" style="background:radial-gradient(ellipse 60% 35% at 60% 55%,#e24aa8,transparent 70%),linear-gradient(135deg,#0c1658,#5a36d0,#1a0f4a)" role="img" aria-label="Blue and pink energy streams"></div>
    <div><div class="event-date">APRIL 18,2025</div><p>Duis aute irure dolor in reprehenderit in voluptate velit esse cillum nulla pariatur.</p><a href="#">Learn More</a></div>
  </article>
  <article class="event abs" style="top:2515px">
    <div class="event-img" style="background:radial-gradient(ellipse 50% 25% at 50% 62%,#9fb2ff,transparent 70%),linear-gradient(180deg,#02040f,#0b1440,#1d2a7a)" role="img" aria-label="Electric spark glowing in the dark"></div>
    <div><div class="event-date">APRIL 18,2025</div><p>Duis aute irure dolor in reprehenderit in voluptate velit esse cillum nulla pariatur.</p><a href="#">Learn More</a></div>
  </article>
</section>

<section class="projects abs">
  <span class="sec-mark abs" style="top:84px"></span>
  <h2 class="sec-title abs" style="top:126px">Our Past <span class="accent">Project</span></h2>
  <div class="project-img" style="left:110px;top:194px;width:346px;height:240px;background:radial-gradient(ellipse 60% 22% at 55% 50%,#b8766a,transparent 75%),radial-gradient(circle at 85% 15%,#eaf4ff,transparent 30%),linear-gradient(135deg,#3a6ea8,#8fb7e0,#2d5d96)" role="img" aria-label="Copper cables with electric arcs"></div>
  <div class="project-img" style="left:470px;top:194px;width:260px;height:240px;background:radial-gradient(ellipse 30% 35% at 65% 75%,#f08a2a,transparent 75%),linear-gradient(100deg,#1c2a40,#3a5272,#2a3545)" role="img" aria-label="Electrician in safety vest working on a panel"></div>
  <div class="project-img" style="left:745px;top:194px;width:345px;height:240px;background:radial-gradient(circle at 55% 35%,#d84a4a,transparent 14%),linear-gradient(90deg,#2a4c7c,#5a7ea8 40%,#d4dde6 70%,#b8c4d0)" role="img" aria-label="Technician checking gauges"></div>
  <div class="project-img" style="left:110px;top:448px;width:346px;height:240px;background:radial-gradient(ellipse 50% 20% at 50% 65%,#b8602e,transparent 75%),linear-gradient(180deg,#3a3a3a,#6a6864 45%,#4a4642)" role="img" aria-label="Cables laid across a warehouse floor"></div>
  <div class="project-img" style="left:470px;top:448px;width:345px;height:240px;background:radial-gradient(ellipse 40% 25% at 30% 40%,#e0a060,transparent 75%),radial-gradient(ellipse 60% 30% at 60% 80%,#2f7fb0,transparent 75%),linear-gradient(160deg,#0a1524,#1c3654,#0d1a2c)" role="img" aria-label="Light trails on a highway at night"></div>
  <div class="project-img" style="left:828px;top:448px;width:262px;height:240px;background:radial-gradient(circle at 35% 22%,#e2b040,transparent 18%),linear-gradient(110deg,#2a3038,#5a5a58,#8a7a5a)" role="img" aria-label="Electrician in hard hat at a switchboard"></div>
  <a class="btn btn-blue" href="#" style="left:526px;top:728px">View More</a>
</section>

<section class="latest-news">
  <span class="sec-mark abs" style="top:3734px"></span>
  <h2 class="sec-title abs" style="top:3778px">Our Latest <span class="accent">News</span></h2>

  <article class="news-card abs" style="left:110px">
    <div class="photo" style="background:radial-gradient(circle at 32% 25%,#e2b040,transparent 16%),radial-gradient(ellipse 40% 35% at 70% 60%,#c4582e,transparent 75%),linear-gradient(160deg,#1a1e28,#3a3e48,#1a1e28)" role="img" aria-label="Electrician wiring a control cabinet"></div>
    <div class="date-badge">OCT 05 2024</div>
    <h4>Lorem ipsum dolor sit</h4>
    <p>Excepteur sint occaecat cupidatat non proident, sunt in culpa qui officia deserunt mollit anim id est laborum.</p>
    <a class="btn btn-blue" href="#">Learn More</a>
  </article>
  <article class="news-card abs" style="left:448px">
    <div class="photo" style="background:radial-gradient(ellipse 50% 30% at 50% 20%,#ffd66a,transparent 75%),linear-gradient(180deg,#c89a3a,#6b7444 45%,#3a4a66 70%,#5a6a86)" role="img" aria-label="Handshake over solar panels"></div>
    <div class="date-badge">OCT 05 2024</div>
    <h4>Lorem ipsum dolor sit</h4>
    <p>Excepteur sint occaecat cupidatat non proident, sunt in culpa qui officia deserunt mollit anim id est laborum.</p>
    <a class="btn btn-blue" href="#">Learn More</a>
  </article>
  <article class="news-card abs" style="left:784px">
    <div class="photo" style="background:radial-gradient(circle at 62% 50%,#ffc24a,transparent 16%),radial-gradient(ellipse 30% 25% at 80% 75%,#e8a040,transparent 75%),linear-gradient(135deg,#0e2a52,#2f5f96,#12305a)" role="img" aria-label="Hand near a glowing light bulb and house"></div>
    <div class="date-badge">OCT 05 2024</div>
    <h4>Lorem ipsum dolor sit</h4>
    <p>Excepteur sint occaecat cupidatat non proident, sunt in culpa qui officia deserunt mollit anim id est laborum.</p>
    <a class="btn btn-blue" href="#">Learn More</a>
  </article>
</section>

<section class="cta abs">
  <svg class="abs" style="left:410px;top:0" width="110" height="270" viewBox="0 0 110 270" aria-hidden="true"><polygon points="84,0 104,0 26,270 6,270" fill="#FFF300"/></svg>
  <h2 class="cta-title abs">Schedule a Free<br>Consultation</h2>
  <div class="contact-item abs" style="left:464px">
    <div class="ico"><svg width="18" height="18" viewBox="0 0 24 24"><path d="M6.6 10.8a15 15 0 0 0 6.6 6.6l2.2-2.2c.3-.3.7-.4 1-.2 1.1.4 2.3.6 3.6.6.6 0 1 .4 1 1V20c0 .6-.4 1-1 1A17 17 0 0 1 3 4c0-.6.4-1 1-1h3.5c.6 0 1 .4 1 1 0 1.3.2 2.5.6 3.6.1.3 0 .7-.2 1z" fill="#0054AA"/></svg></div>
    <strong>PHONE</strong>1-555-014-2290
  </div>
  <div class="contact-item abs" style="left:665px">
    <div class="ico"><svg width="18" height="18" viewBox="0 0 24 24"><path d="M3 5h18v14H3z" fill="#0054AA"/><path d="M3 5l9 7 9-7" fill="none" stroke="#FFF300" stroke-width="2"/></svg></div>
    <strong>Email</strong>jo@brisket-vane.example
  </div>
  <div class="contact-item abs" style="left:888px">
    <div class="ico"><svg width="18" height="18" viewBox="0 0 24 24"><path d="M12 2a7 7 0 0 0-7 7c0 5 7 13 7 13s7-8 7-13a7 7 0 0 0-7-7zm0 9.5A2.5 2.5 0 1 1 12 6.5a2.5 2.5 0 0 1 0 5z" fill="#0054AA"/></svg></div>
    48 Alderbrook<br>Rd. Fernhollow NH 03999
  </div>
</section>

<footer>
  <div class="footer-brand abs"><span class="brand-dot"></span><span class="brand-name">Brisket &amp; Vane</span></div>
  <nav class="footer-nav abs"><a href="#">Home</a><a href="#">About Us</a><a href="#">Services</a><a href="#">Projects</a><a href="#">News</a><a href="#">Contact Us</a></nav>
  <p class="copyright abs">Copyrights@2025.Brisket &amp; Vane.All Rights Reserved</p>
  <div class="social abs" aria-label="Social links"><span></span><span></span><span></span><span></span></div>
</footer>

</body>
</html>
```